Business Cards for a law firm

Business cards for our law firm. Use our silhoette logo and OAK PARTNERS - check our website (www.oakpartners.example)

Contact Information for Business Card

our silhouette logo, OAK PARTNERS, 800-555-0147, Dorian Pemberton, dorian@oakpartners.example

Requirements
Must have
• our silhouette logo, OAK PARTNERS, 800-555-0147, Dorian Pemberton, dorian@oakpartners.example

```html
<!DOCTYPE html>
<html lang="en">
<head>
<meta charset="utf-8">
<title>Oak Partners — Business Cards</title>
<link href="https://fonts.googleapis.com/css2?family=Julius+Sans+One&family=Montserrat:wght@400;500;700&display=swap" rel="stylesheet">
<style>
  :root {
    --navy: #22336b;
    --white: #ffffff;
    --grey: #8c8c8c;
    --ink: #1c2233;
    --backdrop: #e6e7ea;
  }
  * { margin: 0; padding: 0; box-sizing: border-box; }
  html, body { width: 1200px; height: 900px; overflow: hidden; }
  body {
    background: var(--backdrop);
    display: flex;
    flex-direction: column;
    align-items: center;
    justify-content: center;
    gap: 36px;
  }
  .card {
    position: relative;
    width: 700px;
    height: 400px;
    border-radius: 28px;
    overflow: hidden;
    box-shadow: 0 6px 18px rgba(0,0,0,0.18);
  }
  .wordmark {
    display: flex;
    align-items: center;
    gap: 22px;
    font-family: "Julius Sans One", sans-serif;
    font-size: 58px;
    letter-spacing: 2px;
    white-space: nowrap;
  }
  .wordmark-square {
    width: 46px;
    height: 46px;
  }

  /* Front */
  .card-front { background: var(--navy); color: var(--white); }
  .card-front .wordmark {
    position: absolute;
    left: 70px;
    top: 166px;
  }
  .card-front .wordmark-square { background: var(--white); }

  /* Back */
  .card-back { background: var(--white); color: var(--navy); }
  .card-back .wordmark {
    position: absolute;
    left: 60px;
    top: 68px;
  }
  .card-back .wordmark-square { background: var(--navy); }

  .holder {
    position: absolute;
    right: 400px;
    top: 228px;
    text-align: right;
  }
  .holder-name {
    font-family: "Montserrat", sans-serif;
    font-weight: 700;
    font-size: 28px;
    color: var(--navy);
  }
  .holder-title {
    font-family: "Montserrat", sans-serif;
    font-weight: 400;
    font-size: 17px;
    color: var(--ink);
    margin-top: 2px;
  }
  .divider {
    position: absolute;
    left: 322px;
    top: 226px;
    width: 2px;
    height: 72px;
    background: var(--navy);
  }
  .contact-list {
    position: absolute;
    left: 344px;
    top: 228px;
    list-style: none;
    font-family: "Montserrat", sans-serif;
    font-weight: 500;
    font-size: 17px;
    color: var(--ink);
  }
  .contact-list li {
    display: flex;
    align-items: center;
    gap: 10px;
    height: 23px;
  }
  .contact-icon { width: 14px; height: 14px; fill: var(--navy); flex: none; }
  .swoosh { position: absolute; left: 0; bottom: 0; }
</style>
</head>
<body>

  <section class="card card-front">
    <div class="wordmark"><span class="wordmark-square"></span>OAK PARTNERS</div>
  </section>

  <section class="card card-back">
    <div class="wordmark"><span class="wordmark-square"></span>OAK PARTNERS</div>

    <div class="holder">
      <div class="holder-name">Dorian Pemberton</div>
      <div class="holder-title">Attorney at Law</div>
    </div>

    <div class="divider"></div>

    <ul class="contact-list">
      <li>
        <svg class="contact-icon" viewBox="0 0 16 16"><path d="M3 1h3l1 4-2 1a9 9 0 0 0 5 5l1-2 4 1v3a2 2 0 0 1-2 2A13 13 0 0 1 1 3a2 2 0 0 1 2-2z"/></svg>
        800-555-0147
      </li>
      <li>
        <svg class="contact-icon" viewBox="0 0 16 16"><path d="M1 3h14v10H1z M1 3l7 6 7-6" stroke="#fff" stroke-width="1.2"/></svg>
        dorian@oakpartners.example
      </li>
      <li>
        <svg class="contact-icon" viewBox="0 0 16 16"><circle cx="8" cy="8" r="7"/><path d="M1 8h14M8 1c-3 4-3 10 0 14M8 1c3 4 3 10 0 14" stroke="#fff" stroke-width="1" fill="none"/></svg>
        www.oakpartners.example
      </li>
    </ul>

    <svg class="swoosh" width="700" height="140" viewBox="0 0 700 140">
      <path d="M0 20 C140 40 300 60 420 100 C470 118 520 132 560 140 L0 140 Z" fill="var(--navy)"/>
      <path d="M230 55 C380 62 520 100 620 140 L560 140 C500 110 400 78 230 55 Z" fill="var(--grey)"/>
    </svg>
  </section>

</body>
</html>
```